Creative UI design for web application

I need a new UI design for my web application. It will be used by small and micro business owners to plan & implement growth tactics.

I've attached the current design (which I'm open to be changed) - but in particular I need to design the centre of the screen, where the work actually happens.

There needs to be place for a title (YOUR BUSINESS) and description (say 1-2 paragraphs of text) - and am happy to include icons or imagery where makes sense. It may make sense for the user to be able to upload their business logo and name, for example.

This screen will be used by the business owner to understand the real value they offer potential customers and their point of difference - why they exist and why potential customers should care.

They'll use the information they put into this screen to plan things like their messaging.

Following that, there needs to be 2 sections in the dashboard.

The first section is titled "WHO YOU ARE"

The first section will include a number of boxes that the user can input information into, as follows:

- Logo
- Business name
- Business tag line
- Business vision
- Business bio
- Brand colours (these should end up as swatches based on the colour code they enter) - the colour code for each colour swatch should also be visible.
- Key competitors
- SWOT analysis (boxes to enter their strengths, weaknesses, opportunities and threats).

The second section is titled "WHY YOU EXIST"

The second section will include a number of boxes that the user can input information (text) into, as follows:

- Who are your ideal customers?
- What problem are you trying to solve for them?
- What pain points will this remove for them?
- How do you solve it?
- How else could this problem be solved?
- Who offers these other solutions?
- Why is your solution better?
- How much does your solution cost?
- What value are you providing to justify this cost?
- How will this make their life/job easier/better?

They should be able to write a decent amount of information in the boxes.

There should ideally be a place for a description for each of these text fields (for both section 1 & 2) as well so I can give them a little bit more direction around what to put in the box. Alternatively there could be a little icon (say a question mark or "i") that they could click on to view instructions. The instructions will be around 2-4 sentences long for each text field.

You have 2 options:

a) This all needs to appear on the one screen, and the navigation needs to be visible (as per the example attached but feel free to recreate this navigation)

Note: the page can scroll below the fold - but please provide the design for the full length of the page.

b) Potentially the 2 sections could actually be in 2 different items in the menu - YOUR BUSINESS and YOUR VALUE (which would sit next to YOUR BUSINESS and before YOUR CUSTOMER in the screenshot provided). feel free to design them as 2 separate screens if you prefer.

I have attached a screenshot of the app as it stands today (screen shot 2017) which would still exist in the new design but under a different section (the learn section from the plan2 mockup attached)

I have mocked up how this new screen could look if broken into 2 and that's also attached. If you can make this come to life - and look more engaging that would be helpful! :)

Target Market(s)

Small and micro business owners

Industry/Entity Type

Marketing

Number of Pages Required

1 page

Font styles to use
Sans Serif
Other font styles liked:
• Montserrat

Colors
87cfc6
d2a4cc
ffffff
85cae6
e8e8e8
5c5c5c

Requirements
Must have
• Use of my brand colours: #cc8eb2, #76d6c8, #68c7ff as well as white and #595959. Must be visually pleasing / engaging, designed for desktop (as it's a desktop application), really easy to use / navigate.
• Use font Montserrat light & Montserrat Regular or Bold. Mostly should be Montserrat light.
Nice to have
• Would be nice to see how this would look on mobile (as the application is responsive) but this is not mandatory.
Should not have
• Should not look too corporate or dry.

```html
<!DOCTYPE html>
<html lang="en">
<head>
<meta charset="utf-8">
<title>LeafRise – Your Business</title>
<link href="https://fonts.googleapis.com/css2?family=Montserrat:wght@300;400;500;600&display=swap" rel="stylesheet">
<style>
:root{
  --bar-dark:#3b3b3b;
  --footer:#575757;
  --page:#f4f4f4;
  --white:#ffffff;
  --card-head:#85cae6;
  --pink:#d2a4cc;
  --pink-deep:#cc8eb2;
  --text:#5c5c5c;
  --text-soft:#7a7a7a;
  --line:#d9d9d9;
  --border:#e3e3e3;
  --social-1:#3b5998;--social-2:#1da1f2;--social-3:#dd4b39;--social-4:#2e6a91;
}
*{box-sizing:border-box;margin:0;padding:0}
html,body{width:1200px;height:3422px;overflow:hidden}
body{font-family:'Montserrat',sans-serif;font-weight:300;color:var(--text);background:var(--page);position:relative}
.topbar{position:absolute;left:0;top:0;width:1200px;height:62px;background:var(--bar-dark);color:#eee;font-size:16px}
.topbar span{position:absolute;top:21px;white-space:nowrap}
.brand{left:104px;font-weight:500;font-size:19px;color:#fff;letter-spacing:.5px;top:19px!important}
.topbar .active{color:var(--pink)}
.tabs{position:absolute;top:62px;left:0;width:1200px;height:43px;background:var(--white);border-bottom:1px solid var(--border)}
.tab{position:absolute;top:0;height:43px;line-height:43px;font-size:16px;color:#333;font-weight:400;white-space:nowrap}
.tab.current{background:var(--pink);color:#fff;left:98px;width:140px;text-align:center;font-weight:300}
.social{position:absolute;top:0;height:43px;width:49px;display:flex;align-items:center;justify-content:center}
.social i{display:block;width:14px;height:14px;border-radius:50%;background:#fff}
.intro-logo{position:absolute;left:64px;top:146px;width:178px;height:178px;background:var(--white);display:flex;flex-direction:column;align-items:center;justify-content:center;gap:8px}
.intro-logo .dot{width:70px;height:70px;border-radius:50%;background:#222}
.intro-logo .mark{font-size:14px;font-weight:400;color:#222}
.intro-name{position:absolute;left:246px;top:184px;font-size:26px;font-weight:400;color:#222;letter-spacing:.5px}
.contact{position:absolute;left:246px;font-size:15px;color:var(--text-soft);display:flex;align-items:center;gap:8px}
.intro-text{position:absolute;left:98px;top:336px;width:566px;font-size:13px;line-height:26px}
.photo{position:absolute;left:700px;top:182px;width:402px;height:352px;border:6px solid var(--white);box-shadow:0 0 0 1px var(--border);background:linear-gradient(135deg,#c9b59d,#8c7a6a 55%,#5d6c79)}
.rule{position:absolute;left:98px;width:1004px;height:1px;background:var(--line)}
.section-title{position:absolute;left:0;width:1200px;text-align:center;font-size:26px;font-weight:400;color:#222;letter-spacing:1px}
.card{position:absolute;background:var(--white);border:1px solid var(--border)}
.card-head{background:var(--card-head);color:#fff;font-size:16px;font-weight:400;height:41px;line-height:41px;padding:0 22px;text-transform:uppercase;letter-spacing:.5px;white-space:nowrap}
.card-head.question{text-transform:none;line-height:22px;height:56px;padding:6px 60px 0 22px;position:relative;letter-spacing:.3px}
.info{position:absolute;right:18px;top:17px;width:22px;height:22px}
.card-body{padding:26px 22px;font-size:13px;line-height:26px}
.w2{width:486px}.w3{width:315px}
.file-input{position:absolute;left:16px;top:78px;width:454px;height:42px;border:1px solid #ccc}
.browse{position:absolute;left:16px;top:140px;width:110px;height:39px;border-radius:20px;background:var(--pink);color:#fff;font-size:12px;text-align:center;line-height:39px;letter-spacing:1px}
.nofile{position:absolute;left:142px;top:152px;font-size:12px}
.swatches{display:grid;grid-template-columns:repeat(8,50px);gap:6px;padding:28px 24px}
.swatches i{height:50px;display:block}
.swot{display:grid;grid-template-columns:repeat(4,228px);gap:16px;padding:22px 22px}
.swot label{font-size:14px;display:block;margin-bottom:12px}
.swot div div{height:42px;border:1px solid #ccc}
.footer{position:absolute;left:0;top:3353px;width:1200px;height:69px;background:var(--footer);color:#eee;font-size:14px;text-align:center;line-height:69px}
</style>
</head>
<body>
<header class="topbar">
  <span class="brand">LEAFRISE</span>
  <span class="active" style="left:365px">Plan</span>
  <span style="left:436px">Learn</span>
  <span style="left:515px">Remember</span>
  <span style="left:886px"><svg width="14" height="14" viewBox="0 0 14 14" style="vertical-align:-1px"><circle cx="7" cy="4" r="3.2" fill="#eee"/><path d="M1 14c0-4 2.6-6 6-6s6 2 6 6z" fill="#eee"/></svg> My Profile</span>
  <span style="left:1018px"><svg width="15" height="14" viewBox="0 0 15 14" style="vertical-align:-1px"><path d="M6 1H1v12h5M5 7h9M11 4l3 3-3 3" stroke="#eee" stroke-width="1.6" fill="none"/></svg> Log Out</span>
</header>
<nav class="tabs">
  <span class="tab current">Your Business</span>
  <span class="tab" style="left:267px">Your Products</span>
  <span class="tab" style="left:424px">Your Customers</span>
  <span class="tab" style="left:595px">Your Goals</span>
  <span class="tab" style="left:730px">Your Plan</span>
  <span class="social" style="left:906px;background:var(--social-1)"><i></i></span>
  <span class="social" style="left:955px;background:var(--social-2)"><i></i></span>
  <span class="social" style="left:1004px;background:var(--social-3)"><i></i></span>
  <span class="social" style="left:1053px;background:var(--social-4)"><i></i></span>
</nav>

<div class="intro-logo"><span class="dot"></span><span class="mark">Mara Quinn</span></div>
<h1 class="intro-name">MARA QUINN MAKEUP</h1>
<div class="contact" style="top:230px"><svg width="14" height="14"><circle cx="7" cy="7" r="6" fill="#9bb7c9"/></svg>maraquinnmakeup.com</div>
<div class="contact" style="top:259px"><svg width="14" height="12"><rect width="14" height="12" rx="1" fill="#9bb7c9"/><path d="M1 2l6 5 6-5" stroke="#fff" fill="none"/></svg>hello@maraquinnmakeup.com</div>
<p class="intro-text">At vero eos et accusamus et iusto odio dignissimos ducimus qui blanditiis prase ntium voluptatum deleniti atque corrupti quos dolores et quas molestias except uri sint occaecati cupiditate non provident, similique sunt in culpa qui officiades erunt mollitia anim, id est laborum et dolorum fuga. Et harum quidem rerufalis est et expedita distincti m libero tempore, cum soluta nobis est eligendi opticum que nihil impedit quo minus id quod maxime.</p>
<div class="photo" role="img" aria-label="Photo of a makeup artist applying makeup to a client"></div>

<div class="rule" style="top:598px"></div>
<h2 class="section-title" style="top:656px">WHO YOU ARE</h2>

<section class="card w2" style="left:98px;top:728px;height:271px">
  <div class="card-head">Logo</div>
  <div class="file-input"></div>
  <div class="browse">BROWSE</div>
  <span class="nofile">No File Selected</span>
</section>
<section class="card w2" style="left:614px;top:728px;height:271px">
  <div class="card-head">Business Name</div>
  <p class="card-body">Nam libero tempore, cum soluta nobis est eligendi opticumque nihil impedit quo minus id quod maxime placeat facere posmus, omnis voluptas assumenda est, omnis dolor re..</p>
</section>

<section class="card w3" style="left:98px;top:1040px;height:272px">
  <div class="card-head">Business Tag Line</div>
  <p class="card-body">Nam libero tempore, cum soluta nobiest eligendi opticumque nihil impedit qumi nus id quod maxime place.</p>
</section>
<section class="card w3" style="left:442px;top:1040px;height:272px">
  <div class="card-head">Business Vision</div>
  <p class="card-body">Nam libero tempore, cum soluta nobiest eligendi opticumque nihil impedit qumi nus id quod maxime place.</p>
</section>
<section class="card w3" style="left:787px;top:1040px;height:272px">
  <div class="card-head">Business Bio</div>
  <p class="card-body">Nam libero tempore, cum soluta nobiest eligendi opticumque nihil impedit qumi nus id quod maxime place.</p>
</section>

<section class="card w2" style="left:98px;top:1350px;height:274px">
  <div class="card-head">Brand Colours</div>
  <div class="swatches">
    <i style="background:#4a4a55"></i><i style="background:#8a4a25"></i><i style="background:#c8b27a"></i><i style="background:#8c6b4a"></i><i style="background:#d05a7a"></i><i style="background:#b96aa0"></i><i style="background:#4d5a8a"></i><i style="background:#8ab04a"></i>
    <i style="background:#4a4a55"></i><i style="background:#7a8a2a"></i><i style="background:#a2c878"></i><i style="background:#7a8a4a"></i><i style="background:#d4956a"></i><i style="background:#b86a6a"></i><i style="background:#7a4a8a"></i><i style="background:#4ab060"></i>
    <i style="background:#454a4a"></i><i style="background:#8a2a6a"></i><i style="background:#c87aa0"></i><i style="background:#8a4a6a"></i><i style="background:#a25ad0"></i><i style="background:#7a6ab8"></i><i style="background:#4a8a7a"></i><i style="background:#b0604a"></i>
  </div>
</section>
<section class="card w2" style="left:614px;top:1350px;height:274px">
  <div class="card-head">Key Competitors</div>
  <p class="card-body">Nam libero tempore, cum soluta nobis est eligendi opticumque nihil impedit quo minus id quod maxime placeat facere posmus, omnis voluptas assumenda est, omnis dolor re..</p>
</section>

<section class="card" style="left:98px;top:1661px;width:1004px;height:168px">
  <div class="card-head">SWOT Analysis</div>
  <div class="swot">
    <div><label>Strengths</label><div></div></div>
    <div><label>Weaknesses</label><div></div></div>
    <div><label>Opportunities</label><div></div></div>
    <div><label>Threats</label><div></div></div>
  </div>
</section>

<div class="rule" style="top:1909px"></div>
<h2 class="section-title" style="top:1968px">WHY YOU EXIST</h2>

<section class="card w2" style="left:98px;top:2048px;height:272px">
  <div class="card-head question">Who are your ideal<br>customers?<svg class="info" viewBox="0 0 22 22"><circle cx="11" cy="11" r="10" fill="#fff"/><rect x="10" y="9" width="2" height="7" fill="#85cae6"/><circle cx="11" cy="6.5" r="1.3" fill="#85cae6"/></svg></div>
  <p class="card-body">Nam libero tempore, cum soluta nobis est eligendi opticumque nihil impedit quo minus id quod maxime placeat facere posmus, omnis voluptas assumenda est, omnis dolor re..</p>
</section>
<section class="card w2" style="left:614px;top:2048px;height:272px">
  <div class="card-head question">What problem are you trying to<br>solve for them?<svg class="info" viewBox="0 0 22 22"><circle cx="11" cy="11" r="10" fill="#fff"/><rect x="10" y="9" width="2" height="7" fill="#85cae6"/><circle cx="11" cy="6.5" r="1.3" fill="#85cae6"/></svg></div>
  <p class="card-body">Nam libero tempore, cum soluta nobis est eligendi opticumque nihil impedit quo minus id quod maxime placeat facere posmus, omnis voluptas assumenda est, omnis dolor re..</p>
</section>

<section class="card w3" style="left:98px;top:2359px;height:271px">
  <div class="card-head question">How do you<br>solve it?<svg class="info" viewBox="0 0 22 22"><circle cx="11" cy="11" r="10" fill="#fff"/><rect x="10" y="9" width="2" height="7" fill="#85cae6"/><circle cx="11" cy="6.5" r="1.3" fill="#85cae6"/></svg></div>
  <p class="card-body">Nam libero tempore, cum soluta nobiest eligendi opticumque nihil impedit qumi nus id quod maxime place.</p>
</section>
<section class="card w3" style="left:442px;top:2359px;height:271px">
  <div class="card-head question">Who offers these other<br>solutions?<svg class="info" viewBox="0 0 22 22"><circle cx="11" cy="11" r="10" fill="#fff"/><rect x="10" y="9" width="2" height="7" fill="#85cae6"/><circle cx="11" cy="6.5" r="1.3" fill="#85cae6"/></svg></div>
  <p class="card-body">Nam libero tempore, cum soluta nobiest eligendi opticumque nihil impedit qumi nus id quod maxime place.</p>
</section>
<section class="card w3" style="left:787px;top:2359px;height:271px">
  <div class="card-head question">Why is your solution<br>better?<svg class="info" viewBox="0 0 22 22"><circle cx="11" cy="11" r="10" fill="#fff"/><rect x="10" y="9" width="2" height="7" fill="#85cae6"/><circle cx="11" cy="6.5" r="1.3" fill="#85cae6"/></svg></div>
  <p class="card-body">Nam libero tempore, cum soluta nobiest eligendi opticumque nihil impedit qumi nus id quod maxime place.</p>
</section>

<section class="card w2" style="left:98px;top:2671px;height:272px">
  <div class="card-head question">What pain points will this remove<br>for them?<svg class="info" viewBox="0 0 22 22"><circle cx="11" cy="11" r="10" fill="#fff"/><rect x="10" y="9" width="2" height="7" fill="#85cae6"/><circle cx="11" cy="6.5" r="1.3" fill="#85cae6"/></svg></div>
  <p class="card-body">Nam libero tempore, cum soluta nobis est eligendi opticumque nihil impedit quo minus id quod maxime placeat facere posmus, omnis voluptas assumenda est, omnis dolor re..</p>
</section>
<section class="card w2" style="left:614px;top:2671px;height:272px">
  <div class="card-head question">What value are you providing to justify<br>this cost?<svg class="info" viewBox="0 0 22 22"><circle cx="11" cy="11" r="10" fill="#fff"/><rect x="10" y="9" width="2" height="7" fill="#85cae6"/><circle cx="11" cy="6.5" r="1.3" fill="#85cae6"/></svg></div>
  <p class="card-body">Nam libero tempore, cum soluta nobis est eligendi opticumque nihil impedit quo minus id quod maxime placeat facere posmus, omnis voluptas assumenda est, omnis dolor re..</p>
</section>

<section class="card w3" style="left:98px;top:2981px;height:274px">
  <div class="card-head question">How much does your<br>solution cost?<svg class="info" viewBox="0 0 22 22"><circle cx="11" cy="11" r="10" fill="#fff"/><rect x="10" y="9" width="2" height="7" fill="#85cae6"/><circle cx="11" cy="6.5" r="1.3" fill="#85cae6"/></svg></div>
  <p class="card-body">Nam libero tempore, cum soluta nobiest eligendi opticumque nihil impedit qumi nus id quod maxime place.</p>
</section>
<section class="card w3" style="left:442px;top:2981px;height:274px">
  <div class="card-head question">How will this make their<br>life/job easier/better?<svg class="info" viewBox="0 0 22 22"><circle cx="11" cy="11" r="10" fill="#fff"/><rect x="10" y="9" width="2" height="7" fill="#85cae6"/><circle cx="11" cy="6.5" r="1.3" fill="#85cae6"/></svg></div>
  <p class="card-body">Nam libero tempore, cum soluta nobiest eligendi opticumque nihil impedit qumi nus id quod maxime place.</p>
</section>
<section class="card w3" style="left:787px;top:2981px;height:274px">
  <div class="card-head question">How else could this<br>problem be solved?<svg class="info" viewBox="0 0 22 22"><circle cx="11" cy="11" r="10" fill="#fff"/><rect x="10" y="9" width="2" height="7" fill="#85cae6"/><circle cx="11" cy="6.5" r="1.3" fill="#85cae6"/></svg></div>
  <p class="card-body">Nam libero tempore, cum soluta nobiest eligendi opticumque nihil impedit qumi nus id quod maxime place.</p>
</section>

<footer class="footer">Copyright © 2017, LeafRise. All rights reserved.</footer>
</body>
</html>
```